Using attached logo that has been created

Business card with logo that's attached. Maybe with water or the cartoon van in background. Looking for it to not be so plain and not too white.
Information to include;
Rodney Ashcombe
(555) 218-7730
Info@bramleypipeworks.example
www.bramleypipeworks.example
License # 4627195
Looking forward to the designs u come up with.
Thank you!
-Delphine
Target Market(s)
Plumbing
Industry/Entity Type
Plumbing
Contact Information for Business Card
Listed above

```html
<!DOCTYPE html>
<html lang="en">
<head>
<meta charset="utf-8">
<title>Bramley Pipeworks — Business Card</title>
<link rel="stylesheet" href="https://fonts.googleapis.com/css2?family=Michroma&family=Arimo:wght@400&display=swap">
<style>
  :root {
    --stage: #e8e9ec;
    --card-white: #ffffff;
    --brand-blue: #0b5cb5;
    --brand-blue-deep: #0a57ad;
    --brand-blue-bright: #1e74e0;
    --brand-yellow: #f2b705;
    --ink: #1f1f1f;
    --rule: #8a8a8a;
    --art-skin: #c98e6b;
    --art-khaki: #a8926b;
  }
  * { box-sizing: border-box; margin: 0; padding: 0; }
  html, body { width: 1200px; height: 1108px; overflow: hidden; }
  body { background: var(--stage); position: relative; font-family: "Arimo", Arial, sans-serif; }

  .card {
    position: absolute;
    top: 169px;
    width: 440px;
    height: 770px;
    border-radius: 26px;
    overflow: hidden;
    box-shadow: 0 10px 30px rgba(0,0,0,0.15);
  }
  .card--front { left: 130px; background: var(--card-white); }
  .card--back {
    left: 630px;
    background: linear-gradient(160deg, var(--brand-blue-deep) 0%, var(--brand-blue) 50%, var(--brand-blue-deep) 100%);
  }
  .back-pattern {
    position: absolute; inset: 0;
    background: repeating-linear-gradient(-22deg,
      rgba(30,116,224,0) 0 46px,
      rgba(30,116,224,0.35) 46px 78px);
  }

  .mascot-art {
    position: absolute;
    top: 70px; left: 80px;
    width: 280px; height: 360px;
    border-radius: 18px;
    background: linear-gradient(180deg, #f4ece6 0%, #e3ecf8 35%, #cfdcee 60%, #e9e0cf 100%);
  }

  .wordmark {
    position: absolute; top: 458px; left: 0; right: 0;
    text-align: center;
    font-family: "Michroma", sans-serif;
    font-size: 21px;
    color: var(--brand-blue);
    letter-spacing: 1px;
  }
  .wordmark__dot {
    display: inline-block; width: 10px; height: 10px;
    background: var(--brand-yellow); border-radius: 50%;
    margin-right: 10px; vertical-align: middle;
  }

  .person-name {
    position: absolute; top: 512px; left: 0; right: 0;
    text-align: center;
    font-family: "Michroma", sans-serif;
    font-size: 22px;
    color: var(--brand-blue);
    letter-spacing: 2px;
  }

  .contact-icons {
    position: absolute; top: 566px; left: 40px; right: 40px;
    display: flex; align-items: center; gap: 8px;
  }
  .contact-icons__rule { flex: 1; height: 1px; background: var(--rule); }
  .contact-icons__badge {
    width: 36px; height: 36px; border-radius: 7px;
    background: var(--brand-blue);
    display: flex; align-items: center; justify-content: center;
  }

  .contact-list {
    position: absolute; top: 618px; left: 0; right: 0;
    text-align: center; font-size: 19px; line-height: 28px; color: var(--ink);
  }
  .contact-list__domain { color: var(--brand-blue); }

  .license-rule {
    position: absolute; top: 712px; left: 60px; right: 60px;
    height: 1px; background: var(--rule);
  }
  .license {
    position: absolute; top: 724px; left: 0; right: 0;
    text-align: center; font-size: 20px; color: var(--brand-blue);
  }
  .license__number { color: var(--brand-yellow); }
</style>
</head>
<body>
  <section class="card card--front" aria-label="Business card front">
    <div class="mascot-art" role="img" aria-label="Cartoon plumber mascot holding a pipe wrench and a circular saw, in blue shirt and khaki trousers"></div>

    <div class="wordmark"><span class="wordmark__dot"></span>BRAMLEY PIPEWORKS</div>

    <h1 class="person-name">RODNEY ASHCOMBE</h1>

    <div class="contact-icons">
      <span class="contact-icons__rule"></span>
      <span class="contact-icons__badge" aria-label="Phone">
        <svg width="20" height="20" viewBox="0 0 24 24"><path fill="#fff" d="M6.6 10.8a15.1 15.1 0 0 0 6.6 6.6l2.2-2.2c.3-.3.7-.4 1-.2 1.1.4 2.3.6 3.6.6.6 0 1 .4 1 1V20c0 .6-.4 1-1 1A17 17 0 0 1 3 4c0-.6.4-1 1-1h3.5c.6 0 1 .4 1 1 0 1.3.2 2.5.6 3.6.1.3 0 .7-.2 1z"/></svg>
      </span>
      <span class="contact-icons__badge" aria-label="Email">
        <svg width="20" height="20" viewBox="0 0 24 24"><rect x="3" y="5" width="18" height="14" rx="1.5" fill="none" stroke="#fff" stroke-width="2"/><path d="M3.5 6l8.5 7 8.5-7" fill="none" stroke="#fff" stroke-width="2"/></svg>
      </span>
      <span class="contact-icons__badge" aria-label="Website">
        <svg width="20" height="20" viewBox="0 0 24 24" fill="none" stroke="#fff" stroke-width="1.8"><circle cx="12" cy="12" r="9"/><ellipse cx="12" cy="12" rx="4" ry="9"/><path d="M3 12h18M5 7h14M5 17h14"/></svg>
      </span>
      <span class="contact-icons__rule"></span>
    </div>

    <div class="contact-list">
      <p>(555) 218-7730</p>
      <p>Info@bramleypipeworks.example</p>
      <p>www.<span class="contact-list__domain">bramleypipeworks</span>.example</p>
    </div>

    <div class="license-rule"></div>
    <p class="license">License <span class="license__number"># 4627195</span></p>
  </section>

  <section class="card card--back" aria-label="Business card back">
    <div class="back-pattern" role="img" aria-label="Repeating diagonal brand wordmark pattern in lighter blue"></div>
  </section>
</body>
</html>
```